Dynamic Business Card for Sports Supplements Company

Hi! I'm looking for an awesome business card to match my existing sports supplement company. I have uploaded my current company logo and screenshot of the front page of my website.

I would like to have something dynamic and interesting and utilize the colors in the website - the reds and purples

The business card should be double sided and focus on a unique eye-catching design on the back and include all the relevant company info.

Most importantly, it should say somewhere: "Sign up on our website for a coupon code."

Target Market(s)

Mostly for women gym goers but it shouldn't be too feminine. It should be in keeping with the website design. It should flow and clearly be connected to it

Industry/Entity Type

Business

Contact Information for Business Card

Lorraine K. Vestal
CEO
LVestal@Quorvanexco.com
www.quorvanexco.com
555.417.3820
P.O. Box 47315
Halvern, Westmark 00000

Sign up on our website for a coupon code

Font styles to use
Serif
Sans Serif
Other font styles liked:
• Novecento font family and "Quorvanex" is in AR Destine font

Requirements
Must have
• One side should be a bold Quorvanex logo design. Even just the symbol itself may be o.k. (see attached file)

```html
<!DOCTYPE html>
<html lang="en">
<head>
<meta charset="utf-8">
<title>Quorvanex Business Card</title>
<link rel="stylesheet" href="https://fonts.googleapis.com/css2?family=Open+Sans:wght@400;500;600;700&display=swap">
<style>
  :root {
    --page-bg: #000000;
    --slate-light: #454b56;
    --slate-dark: #22262d;
    --violet-light: #5d4fa6;
    --violet-dark: #2f2860;
    --accent-red: #e0222d;
    --text-white: #ffffff;
    --text-soft: #d9dbe2;
  }
  * { margin: 0; padding: 0; box-sizing: border-box; }
  html, body {
    width: 1200px; height: 900px; overflow: hidden;
    background: var(--page-bg);
    font-family: "Open Sans", Arial, sans-serif;
  }
  .canvas { position: relative; width: 1200px; height: 900px; }
  .card {
    position: absolute; top: 271px; width: 457px; height: 281px;
    border-radius: 14px; overflow: hidden;
  }
  .card--front {
    left: 137px;
    background: radial-gradient(ellipse at 35% 20%, var(--slate-light), var(--slate-dark) 80%);
  }
  .card--back {
    left: 627px;
    background: radial-gradient(ellipse at 40% 15%, var(--violet-light), var(--violet-dark) 85%);
  }
  .brand {
    position: absolute; text-align: center; color: var(--text-white);
  }
  .brand__name {
    font-weight: 700; font-size: 27px; letter-spacing: 1px; line-height: 1;
  }
  .brand__tagline {
    font-size: 9px; letter-spacing: 1.6px; color: var(--text-soft); margin-top: 3px;
  }
  .card--front .brand { left: 20px; width: 214px; top: 160px; }
  .card--back .brand { left: 0; width: 457px; top: 168px; }
  .contact { position: absolute; left: 245px; top: 70px; color: var(--text-white); }
  .contact__name {
    color: var(--accent-red); font-size: 16px; font-weight: 500; letter-spacing: 0.5px;
    text-transform: uppercase; line-height: 20px;
  }
  .contact__title { font-size: 12.5px; margin-top: 1px; padding-left: 2px; }
  .contact__list { list-style: none; margin-top: 10px; padding-left: 2px; }
  .contact__item {
    display: flex; align-items: center; gap: 6px; font-size: 12.5px; line-height: 20.5px;
  }
  .contact__icon { width: 12px; height: 12px; fill: var(--accent-red); flex: none; }
  .contact__address { font-size: 12.5px; line-height: 18px; margin-top: 9px; padding-left: 2px; }
  .promo {
    position: absolute; left: 0; width: 457px; top: 231px; text-align: center;
    color: var(--text-white); font-size: 12.5px; letter-spacing: 0.3px; text-transform: uppercase;
  }
  .promo__link { color: var(--accent-red); }
</style>
</head>
<body>
<main class="canvas">
  <section class="card card--front">
    <div class="brand">
      <div class="brand__name">QUORVANEX</div>
      <div class="brand__tagline">YOUR TRAINING COMPANION</div>
    </div>
    <div class="contact">
      <div class="contact__name">Lorraine K. Vestal</div>
      <div class="contact__title">CEO</div>
      <ul class="contact__list">
        <li class="contact__item">
          <svg class="contact__icon" viewBox="0 0 12 12" aria-hidden="true"><path d="M1 4 Q6 0 11 4 L9.5 5.5 L8 4.5 L8 3.5 Q6 2.8 4 3.5 L4 4.5 L2.5 5.5 Z M3 6 H9 L10 11 H2 Z"/></svg>
          <span>555.417.3820</span>
        </li>
        <li class="contact__item">
          <svg class="contact__icon" viewBox="0 0 12 12" aria-hidden="true"><path d="M1 2.5 H11 V3.3 L6 6.8 L1 3.3 Z M1 4.5 L6 8 L11 4.5 V9.5 H1 Z"/></svg>
          <span>LVestal@Quorvanexco.com</span>
        </li>
        <li class="contact__item">
          <svg class="contact__icon" viewBox="0 0 12 12" aria-hidden="true"><circle cx="6" cy="6" r="5.2"/></svg>
          <span>www.quorvanexco.com</span>
        </li>
      </ul>
      <div class="contact__address">P.O. Box 47315<br>Halvern, Westmark 00000</div>
    </div>
  </section>

  <section class="card card--back">
    <div class="brand">
      <div class="brand__name">QUORVANEX</div>
      <div class="brand__tagline">YOUR TRAINING COMPANION</div>
    </div>
    <p class="promo">Sign up on our <span class="promo__link">website</span> for a coupon code</p>
  </section>
</main>
</body>
</html>
```